Website Development for vaultmerrow.com.au

Build a new Wordpress/Responsive website for vaultmerrow.com.au

Target Market(s)

Compliance Managers, Risk Managers, Information Security and Cyber Security Professionals, Chief Data/Digital Officers, Chief Operating/Financial Officers, Business Continuity Professionals, Disaster Recovery Planners, Small Business Owners, Local/Federal Government entities

Industry/Entity Type

Data Service

Coding

Coded - Design and coding required

Number of Pages Required

5+ page

Font styles to use
Sans Serif

Colors

Designer to choose colors to be used in the design.

Requirements
Must have
• 1. Site Structure: Home Page plus the following chapter-pages for a) Services b) About c) Resources d) Blog e) Contact Us
• 2. Prefer site to built on wordpress and we can purchase a theme if needed (we currently use Kelp9 for other sites)
• 3. Blog needs to be wordpress based
• 4. We will host the site ourselves on our own servers
• 5. Responsive Design
Nice to have
• 1. Livechat capability/interface
• 2. Capability for marketing automation integration (such as hubspot, marketo, infusionsoft etc)
• 3. Capability for CRM integration (Salesforce)

```html
<!DOCTYPE html>
<html lang="en">
<head>
<meta charset="UTF-8">
<title>Vaultmerrow – Resources</title>
<link href="https://fonts.googleapis.com/css2?family=Roboto:wght@400;500;700&family=Roboto+Condensed:wght@400;700&family=Montserrat:wght@400;500&display=swap" rel="stylesheet">
<style>
:root{
  --red:#e3232a;
  --red-deep:#8e0f14;
  --grey-bar:#9b9b9d;
  --grey-foot:#8e8e91;
  --ink:#2b2b2b;
  --text:#444;
  --soft:#f4f4f4;
  --white:#fff;
}
*{box-sizing:border-box;margin:0;padding:0}
html,body{width:743px;height:1200px;overflow:hidden}
body{position:relative;background:var(--white);font-family:"Montserrat",sans-serif;color:var(--text)}
.topbar{position:absolute;left:0;top:0;width:743px;height:30px;background:var(--grey-bar);color:var(--white);font-family:"Roboto",sans-serif;font-size:8.5px}
.topbar .contact{position:absolute;top:10px;display:flex;align-items:center;gap:6px}
.topbar .social{position:absolute;right:88px;top:8px;display:flex;align-items:center;gap:5px;font-weight:700}
.topbar .social span.sq{width:13px;height:13px;display:inline-block}
.header{position:absolute;top:30px;left:0;width:743px;height:50px;background:#f8f8f8}
.brand{position:absolute;left:88px;top:12px;display:flex;align-items:center;gap:5px;font-family:"Roboto",sans-serif;font-weight:500;font-size:19px;color:var(--red)}
.brand .dot{width:18px;height:18px;border-radius:50%;background:var(--red)}
.nav{position:absolute;right:89px;top:24px;display:flex;gap:20px;font-family:"Roboto",sans-serif;font-size:8.8px;color:#333}
.nav .active{color:var(--red);position:relative}
.nav .active::after{content:"";position:absolute;left:1px;right:1px;top:17px;height:3px;background:var(--red)}
.hero{position:absolute;top:80px;left:0;width:743px;height:218px;background:radial-gradient(circle at 75% 40%,#e2272e 0,#b5161c 30%,#5e0a0d 75%,#3a0507 100%);overflow:hidden}
.hero .visual{position:absolute;left:400px;top:0;width:343px;height:218px}
.hero h1{position:absolute;left:88px;top:36px;font-family:"Roboto Condensed",sans-serif;font-weight:400;font-size:27px;line-height:33px;color:var(--white)}
.hero h1 b{font-weight:700}
.hero p{position:absolute;left:88px;top:135px;font-family:"Roboto",sans-serif;font-size:17px;color:var(--white)}
.hero svg.curve{position:absolute;left:0;bottom:0}
.crumbs{position:absolute;top:297px;left:0;width:743px;height:28px;background:var(--soft);font-family:"Roboto",sans-serif;font-size:9px;color:#333;padding:7px 0 0 88px}
.crumbs b{color:var(--red);font-weight:500;margin-left:6px}
.crumbs i{font-style:normal;margin-left:6px}
.intro{position:absolute;top:366px;left:0;width:743px;text-align:center}
.intro h2{font-family:"Roboto Condensed",sans-serif;font-weight:700;font-size:27px;color:var(--ink);letter-spacing:.3px}
.intro p{width:440px;margin:12px auto 0;font-size:7px;line-height:12px;color:#333}
.resources{position:absolute;top:460px;left:116px;width:511px;list-style:none}
.resources li{height:59.5px;background:var(--white);box-shadow:0 1px 4px rgba(0,0,0,.12);position:relative;border-bottom:1px solid #eee}
.resources svg{position:absolute;left:18px;top:12px}
.resources h3{position:absolute;left:75px;top:10px;font-family:"Roboto",sans-serif;font-weight:500;font-size:10.5px;color:var(--ink)}
.resources p{position:absolute;left:75px;top:26px;width:425px;font-size:6.9px;line-height:12px;color:#444}
.start{position:absolute;top:801px;left:0;width:743px;height:290px;background:linear-gradient(180deg,#e2343a,#d92a31);overflow:hidden}
.start h2{position:absolute;top:62px;width:743px;text-align:center;font-family:"Roboto Condensed",sans-serif;font-weight:700;font-size:26px;color:var(--white)}
.form{position:absolute;left:194px;top:116px;width:398px;height:88px;border:1px solid rgba(255,255,255,.6);display:flex}
.form .col{width:200px;border-right:1px solid rgba(255,255,255,.6)}
.form .field{height:29px;padding:9px 0 0 11px;font-size:7.5px;color:rgba(255,255,255,.75);border-bottom:1px solid rgba(255,255,255,.35)}
.form .field:first-child{color:var(--white);border-bottom:1.5px solid var(--white)}
.form .field:last-child{border-bottom:0}
.form .msg{padding:9px 0 0 13px;font-size:7.5px;color:rgba(255,255,255,.75)}
.submit{position:absolute;left:332px;top:224px;width:79px;height:22px;border-radius:11px;background:#111;color:var(--white);font-family:"Roboto",sans-serif;font-weight:500;font-size:9.5px;padding:5px 0 0 29px}
.submit::before{content:"";position:absolute;left:4px;top:4px;width:14px;height:14px;border-radius:50%;background:var(--red)}
.chat{position:absolute;z-index:5;left:631px;top:1076px;width:27px;height:27px;border-radius:50%;background:var(--white);box-shadow:0 2px 5px rgba(0,0,0,.3)}
.footer{position:absolute;top:1091px;left:0;width:743px;height:109px;background:var(--grey-foot);color:var(--white)}
.footer .brand{top:30px;color:var(--white);font-size:23px}
.footer .brand .dot{width:22px;height:22px;background:var(--white)}
.footer .nav{top:46px;right:92px;gap:25px;color:var(--white);font-size:8.3px}
.footer hr{position:absolute;left:88px;right:88px;top:82px;border:0;border-top:1px solid rgba(255,255,255,.3)}
.footer .legal{position:absolute;top:92px;font-size:6.8px}
</style>
</head>
<body>

<div class="topbar">
  <div class="contact" style="left:88px">
    <svg width="11" height="11" viewBox="0 0 12 12" fill="none" stroke="#fff" stroke-width="1"><path d="M3 1l2 3-1.3 1.2c.7 1.4 1.7 2.4 3.1 3.1L8 7l3 2-1 2C5.5 11 1 6.5 1 2z"/></svg>
    <span>+061-482-905</span>
  </div>
  <div class="contact" style="left:180px">
    <svg width="12" height="9" viewBox="0 0 12 9" fill="none" stroke="#fff" stroke-width="1"><rect x=".5" y=".5" width="11" height="8"/><path d="M.5 .5L6 5l5.5-4.5"/></svg>
    <span>info@vaultmerrow.com</span>
  </div>
  <div class="social">
    <span>Follow Us on</span>
    <span class="sq" style="background:#e04a3a"></span>
    <span class="sq" style="background:#2aa3e0"></span>
    <span class="sq" style="background:#1f6aa8"></span>
    <span class="sq" style="background:#e33a2f"></span>
  </div>
</div>

<header class="header">
  <div class="brand"><span class="dot"></span>Vaultmerrow</div>
  <nav class="nav">
    <span>HOME</span><span>ABOUT</span><span>SERVICES</span><span class="active">RESOURCES</span><span>BLOG</span><span>CONTACT US</span>
  </nav>
</header>

<section class="hero">
  <div class="visual" role="img" aria-label="Hands holding a glowing red sphere covered in hexagonal technology and security icons" style="background:radial-gradient(circle at 42% 48%,#f2474c 0,#c81c23 28%,rgba(120,10,14,0) 60%)"></div>
  <h1>DELIVERING <b>QUALITY</b><br>SERVICES THROUGH<br><b>INNOVATION</b></h1>
  <p>From Industry&nbsp; Experts</p>
  <svg class="curve" width="743" height="70" viewBox="0 0 743 70" preserveAspectRatio="none"><path d="M0 38 C150 75 450 92 743 8 L743 70 L0 70 Z" fill="#f4f4f4"/></svg>
</section>

<div class="crumbs">HOME <i>»</i> <b>RESOURCES</b></div>

<section class="intro">
  <h2>RESOURCES</h2>
  <p>The point of using Lorem Ipsum is that it has a more-or-less normal distribution of letters, as opposed to using ‘Content here, content here’, making it look like readable English</p>
</section>

<ul class="resources">
  <li>
    <svg width="40" height="36" viewBox="0 0 40 36" fill="none" stroke="#777" stroke-width="1.4"><path d="M16 2L1 29h24"/><path d="M16 2l10 18"/><path d="M16 11v9"/><circle cx="16" cy="24" r=".8" fill="#777"/><circle cx="29" cy="27" r="8"/><circle cx="29" cy="24.5" r="2.3"/><path d="M25 32c1-3 7-3 8 0"/></svg>
    <h3>Risk Managers</h3>
    <p>Lorem Ipsum is that it has a more-or-less&nbsp; normal distribution of letters, as opposed to using ‘Content here, content here’, making it look like readable English has a more-or-less&nbsp; normal</p>
  </li>
  <li>
    <svg width="40" height="36" viewBox="0 0 40 36" fill="none" stroke="#777" stroke-width="1.4"><path d="M20 1c5 3 9 4 14 4v12c0 9-7 14-14 18C13 31 6 26 6 17V5c5 0 9-1 14-4z"/><path d="M20 5c4 2 7 3 10 3v9c0 6-5 10-10 13-5-3-10-7-10-13V8"/><path d="M14 18l5 5 8-9"/></svg>
    <h3>Information Security</h3>
    <p>Lorem Ipsum is that it has a more-or-less&nbsp; normal distribution of letters, as opposed to using ‘Content here, content here’, making it look like readable English has a more-or-less&nbsp; normal</p>
  </li>
  <li>
    <svg width="40" height="38" viewBox="0 0 40 38" fill="none" stroke="#777" stroke-width="1.3"><rect x="8" y="7" width="24" height="24"/><rect x="13" y="12" width="14" height="14"/><rect x="16.5" y="18" width="7" height="6"/><path d="M18 18v-2a2 2 0 0 1 4 0v2"/><path d="M13 1v6M18 1v6M23 1v6M28 1v6M13 31v6M18 31v6M23 31v6M28 31v6M2 12h6M2 17h6M2 22h6M2 27h6M32 12h6M32 17h6M32 22h6M32 27h6"/></svg>
    <h3>Cyber Security Professionals</h3>
    <p>Lorem Ipsum is that it has a more-or-less&nbsp; normal distribution of letters, as opposed to using ‘Content here, content here’, making it look like readable English has a more-or-less&nbsp; normal</p>
  </li>
  <li>
    <svg width="40" height="36" viewBox="0 0 40 36" fill="none" stroke="#777" stroke-width="1.3"><circle cx="17" cy="7" r="5"/><path d="M10 20c0-5 14-5 14 0"/><rect x="6" y="20" width="24" height="6"/><rect x="9" y="26" width="18" height="8"/><path d="M28 5h5M28 8h5M28 11h5"/></svg>
    <h3>Chief Data Technicians</h3>
    <p>Lorem Ipsum is that it has a more-or-less&nbsp; normal distribution of letters, as opposed to using ‘Content here, content here’, making it look like readable English has a more-or-less&nbsp; normal</p>
  </li>
  <li>
    <svg width="40" height="36" viewBox="0 0 40 36" fill="none" stroke="#777" stroke-width="1.3"><path d="M13 6c0-4 14-4 14 0v2H13z"/><circle cx="20" cy="12" r="6"/><path d="M6 35c0-10 5-13 14-13s14 3 14 13"/><path d="M20 22v13M24 27h5v5h-5z"/></svg>
    <h3>Digital Officers</h3>
    <p>Lorem Ipsum is that it has a more-or-less&nbsp; normal distribution of letters, as opposed to using ‘Content here, content here’, making it look like readable English has a more-or-less&nbsp; normal</p>
  </li>
</ul>

<section class="start">
  <div role="img" aria-label="Team meeting around a table with laptops, tinted red" style="position:absolute;inset:0;background:linear-gradient(120deg,rgba(170,20,25,.25),rgba(255,255,255,0) 50%,rgba(160,20,25,.3))"></div>
  <h2>LET’S GET STARTED</h2>
  <div class="form">
    <div class="col">
      <div class="field">Your Name*</div>
      <div class="field">Your Email*</div>
      <div class="field">Your Contact Number*</div>
    </div>
    <div class="msg">Your Message*</div>
  </div>
  <div class="submit">Submit</div>
</section>

<footer class="footer">
  <div class="brand"><span class="dot"></span>Vaultmerrow</div>
  <nav class="nav"><span>HOME</span><span>ABOUT</span><span>SERVICES</span><span>RESOURCES</span><span>BLOG</span><span>CONTACT US</span></nav>
  <hr>
  <div class="legal" style="left:88px">Copyright 2019 @ Vaultmerrow. All Rights Reserved.</div>
  <div class="legal" style="right:91px">Terms of Services / Privacy Policy</div>
</footer>

<div class="chat" aria-label="Live chat">
  <svg width="27" height="27" viewBox="0 0 26 26"><ellipse cx="14" cy="13" rx="6" ry="4.5" fill="#e3232a"/><path d="M10 16l-2 3 4-2z" fill="#e3232a"/><circle cx="12" cy="13" r=".8" fill="#fff"/><circle cx="14" cy="13" r=".8" fill="#fff"/><circle cx="16" cy="13" r=".8" fill="#fff"/><circle cx="21" cy="3.5" r="2.5" fill="#e3232a"/></svg>
</div>

</body>
</html>
```